Velvet Riot Rising Line of Sparkling Wine & Spirits

Back info: Nora Beth Quill Owner 555-318-4402 1480 E. Harlow Ave, Bldg. 2, & 3, Lodi Ca. 95871
Sparkling Wines & Memorabilia www.velvetriotrising.com
Ok I have uploaded the winning design. The color that I am after is the Fushia, Raspberry, Red, Matte Satin Matalic Finish. With a 24 Karet Gold color Foil. The Bottle is on the top row and it's the 2nd Bottle in. That is the Color that I want. This is the style of font. Make sure that you put what we're advertising. Good Luck to you all. Warmest regards, Nora
21 & up UniSex
Sparkling Wine and Memorabilia
there listed up above.....

```html
<!DOCTYPE html>
<html lang="en">
<head>
<meta charset="utf-8">
<title>Velvet Riot Rising – Business Card</title>
<link href="https://fonts.googleapis.com/css2?family=Quicksand:wght@400;500;600&family=Poppins:wght@500&display=swap" rel="stylesheet">
<style>
  :root {
    --stage: #c9c9c9;
    --fuchsia: #e0168f;
    --fuchsia-deep: #b30f6f;
    --raspberry: #8f0a55;
    --noir: #1d0612;
    --noir-plum: #3a0d28;
    --gold: #f2cf63;
  }
  * { box-sizing: border-box; margin: 0; padding: 0; }
  html, body { width: 1200px; height: 800px; overflow: hidden; }
  body {
    background: var(--stage);
    display: flex;
    align-items: center;
    justify-content: center;
    gap: 40px;
    font-family: "Quicksand", sans-serif;
  }
  .card {
    position: relative;
    width: 560px;
    height: 320px;
    overflow: hidden;
    box-shadow: 0 10px 28px rgba(0,0,0,0.28);
  }

  /* Info side */
  .card--info {
    background: linear-gradient(160deg, var(--fuchsia-deep) 0%, var(--fuchsia) 55%, var(--fuchsia-deep) 100%);
  }
  .feature-art {
    position: absolute;
    top: 0; right: 0;
    width: 230px; height: 200px;
    background: linear-gradient(200deg, var(--noir) 0%, var(--noir-plum) 55%, var(--raspberry) 100%);
  }
  .contact {
    position: absolute;
    left: 40px; top: 40px;
    width: 280px;
    color: var(--gold);
  }
  .contact__name {
    font-size: 30px;
    font-weight: 500;
    letter-spacing: 0.5px;
    line-height: 1.1;
  }
  .contact__role {
    font-size: 16px;
    margin-bottom: 22px;
  }
  .contact__list { list-style: none; }
  .contact__item {
    display: flex;
    align-items: center;
    gap: 10px;
    font-size: 16px;
    font-weight: 500;
    line-height: 1.5;
    white-space: nowrap;
  }
  .contact__item svg { width: 14px; height: 14px; flex: none; }
  .contact__address {
    margin-top: 18px;
    padding-left: 24px;
    font-size: 16px;
    font-weight: 500;
    line-height: 1.35;
  }
  .social {
    position: absolute;
    left: 64px; bottom: 24px;
    display: flex;
    align-items: center;
    gap: 10px;
    color: var(--gold);
    font-size: 14px;
    font-weight: 500;
  }
  .social__dot {
    width: 26px; height: 26px;
    border: 2px solid var(--gold);
    border-radius: 50%;
  }

  /* Brand side */
  .card--brand {
    background: radial-gradient(ellipse at 50% 45%, var(--fuchsia) 0%, var(--fuchsia-deep) 70%, var(--raspberry) 100%);
    display: flex;
    flex-direction: column;
    align-items: center;
    justify-content: center;
    gap: 46px;
  }
  .brand-name {
    font-weight: 600;
    font-size: 44px;
    color: var(--noir);
    letter-spacing: 0.5px;
  }
  .tagline {
    font-family: "Poppins", sans-serif;
    font-weight: 500;
    font-size: 19px;
    color: var(--gold);
    letter-spacing: 0.3px;
  }
</style>
</head>
<body>

<section class="card card--info">
  <div class="feature-art" role="img" aria-label="Illustration of a fuchsia sparkling wine bottle with gold foil neck over a dark ornamental pattern"></div>

  <div class="contact">
    <h1 class="contact__name">Nora Beth Quill</h1>
    <p class="contact__role">Owner</p>
    <ul class="contact__list">
      <li class="contact__item">
        <svg viewBox="0 0 24 24" fill="none" stroke="currentColor" stroke-width="2.4"><path d="M5 3h4l2 5-3 2a12 12 0 0 0 6 6l2-3 5 2v4a2 2 0 0 1-2 2A18 18 0 0 1 3 5a2 2 0 0 1 2-2z"/></svg>
        555-318-4402
      </li>
      <li class="contact__item">
        <svg viewBox="0 0 24 24" fill="none" stroke="currentColor" stroke-width="2.4"><rect x="2" y="5" width="20" height="14"/><path d="M2 5l10 8 10-8"/></svg>
        thequeen@velvetriotrising.com
      </li>
      <li class="contact__item">
        <svg viewBox="0 0 24 24" fill="none" stroke="currentColor" stroke-width="2.4"><circle cx="12" cy="12" r="10"/><path d="M2 12h20M12 2c3 3 3 17 0 20M12 2c-3 3-3 17 0 20"/></svg>
        www.velvetriotrising.com
      </li>
    </ul>
    <p class="contact__address">1480 E. Harlow Ave,<br>Bldg. 2, &amp; 3, Lodi Ca. 95871</p>
  </div>

  <div class="social">
    <span class="social__dot"></span>
    <span>Velvet Riot Rising</span>
  </div>
</section>

<section class="card card--brand">
  <h2 class="brand-name">Velvet Riot Rising</h2>
  <p class="tagline">LINE OF SPARKLING WINE &amp; SPIRITS</p>
</section>

</body>
</html>
```